Teeth Whitening Clinic Website Redesign - Social Proof Theme

NEW TEETH SITEREVAMP CURRENT WEBSITE:WWW.SANDIEGOSTEETHWHITENING.COMTHEME:SOCIAL PROOF/5 STAR REVIEWS/TESTIMONIALS THEME:https://maps.example.net/QxRvPLoKzN84 I want a testimonial themed, social proof themed website so customers will be sold by testimonials all over the website….I like a nice clean simple site but with all important factors standing out like CALLS TO ACTIONS, for example the $99 special link in header on original design. Also, testimonials throughout the website placed methodically as not to be FORCED and CLUTTEREDKeep all same exact content for all pages and elements of current design. All buttons, calls to action, navigation, etc. Please do not leave anything out from current design. SPECIAL INSTRUCTIONS for banner image:I want to use actual customer photos inside the banner image in a way that really pops and grabs attention. Please grab some customer photos from my PG Account, fk or rateway account: Also, I want to integrate 5 star rateway logo, friendbook review 5 stars icon, searchly business page 5 stars icon, etc. on the banner as well to show social proof as much as possible. Actual customer photos to be used throughout website:https://www.photogram.example/brightharborsmilestudioplace/ https://www.friendbook.com/SDTeethWhitening/https://www.reviewhub.example/biz/bright-harbor-smile-studio-place-bright-harbor-5 Reviews:https://www.reviewhub.example/biz/bright-harbor-smile-studio-place-bright-harbor-5 https://www.friendbook.com/pg/SDTeethWhitening/reviews/?ref=page_internalhttps://goo.gl/maps/TmJcABLAJwC2 Please do home page first to come up with theme then after approval home page we can move forward additional pages.

Target Market(s)

PEOPLE THAT CARE ABOUT DENTAL HYGEINE AND OR CARE ABOUT THEIR TEETH SMILE

Industry/Entity Type

Dental Clinic

Number of Pages Required

5+ page

Colors

Designer to choose colors to be used in the design.

Requirements
Must have
• NEW TEETH SITE
• REVAMP CURRENT WEBSITE:
• WWW.BRIGHTHARBORSMILESTUDIO.EXAMPLE
• THEME:
• SOCIAL PROOF/5 STAR REVIEWS/TESTIMONIALS THEME:
• https://maps.example.net/QxRvPLoKzN84
• I want a testimonial themed, social proof themed website so customers will be sold by testimonials all over the website….I like a nice clean simple site but with all important factors standing out like CALLS TO ACTIONS, for example the $99 special link in header on original design. Also, testimonials throughout the website placed methodically as not to be FORCED and CLUTTERED
• Keep all same exact content for all pages and elements of current design. All buttons, calls to action, navigation, etc. Please do not leave anything out from current design.
• SPECIAL INSTRUCTIONS for banner image:
• I want to use actual customer photos inside the banner image in a way that really pops and grabs attention. Please grab some customer photos from my PG Account, fk or rateway account:
• Also, I want to integrate 5 star rateway logo, friendbook review 5 stars icon, searchly business page 5 stars icon, etc. on the banner as well to show social proof as much as possible.
• Actual customer photos to be used throughout website:
• https://www.photogram.example/brightharborsmilestudioplace/
• https://www.friendbook.example/BHSmileStudio/
• https://www.reviewhub.example/biz/bright-harbor-smile-studio-place-bright-harbor-5
• Reviews:
• https://www.friendbook.example/pg/BHSmileStudio/reviews/?ref=page_internal
• Please do home page first to come up with theme then after approval home page we can move forward additional pages.
Nice to have
• NEW TEETH SITE
• REVAMP CURRENT WEBSITE:
• THEME:
• Reviews:
Should not have
• NEW TEETH SITE
• REVAMP CURRENT WEBSITE:
• THEME:
• Reviews:

```html
<!DOCTYPE html>
<html lang="en">
<head>
<meta charset="utf-8">
<title>Bright Harbor Smile Studio – Home</title>
<link href="https://fonts.googleapis.com/css2?family=Roboto:wght@400;500;700;900&display=swap" rel="stylesheet">
<style>
:root{
  --cyan:#36c0dc;
  --cyan-deep:#1fa9c8;
  --cyan-soft:#7fd6e8;
  --dark:#2d2d2d;
  --ink:#333;
  --muted:#666;
  --footer:#5b5b5b;
  --white:#fff;
  --light:#f1f3f4;
}
*{box-sizing:border-box;margin:0;padding:0}
html,body{width:1200px;height:3854px;overflow:hidden}
body{font-family:"Roboto",Arial,sans-serif;color:var(--ink);background:var(--white);position:relative}
.abs{position:absolute}
section,header,footer,nav{position:absolute;left:0;width:1200px}
.caps{text-transform:uppercase}

/* top bar */
.topbar{top:0;left:0;width:1200px;height:51px;border-bottom:1px solid #e5e5e5;font-size:11px;color:var(--ink)}
.topbar .hours{left:172px;top:18px;white-space:nowrap}
.topbar b{font-weight:700}
.topbar .social{right:172px;top:17px;display:flex;gap:10px;font-size:10px;color:var(--muted);white-space:nowrap}

/* header */
.masthead{top:51px;height:85px}
.logo{left:172px;top:14px;display:flex;align-items:center;gap:10px}
.logo .dot{width:56px;height:56px;border-radius:50%;background:#dfe9ee}
.logo .name{font-size:26px;font-weight:500;color:#3a3a3a;line-height:1;white-space:nowrap}
.logo .name small{display:block;font-size:12px;color:var(--cyan-deep);margin-top:4px;letter-spacing:.5px}
.contact-item{top:22px;display:flex;gap:12px;font-size:11px;color:var(--muted);white-space:nowrap}
.contact-item strong{display:block;font-size:12px;color:var(--ink);margin-bottom:3px}
.contact-item svg{flex:none;margin-top:2px}
.contact-address{left:585px}
.contact-phone{left:918px}

/* nav */
.mainnav{top:136px;height:39px;background:var(--dark)}
.mainnav ul{list-style:none;position:absolute;left:172px;top:0;display:flex;height:39px;align-items:center;gap:24px;white-space:nowrap}
.mainnav li{color:var(--white);font-size:11px;font-weight:700}
.mainnav .book{position:absolute;right:172px;top:4px;height:31px;width:139px;background:var(--cyan);color:var(--white);font-size:11px;font-weight:700;display:flex;align-items:center;justify-content:center}

/* hero */
.hero{top:175px;height:437px;background:linear-gradient(90deg,#4fc7df 0%,#36c0dc 45%,#5cc9e0 100%);overflow:hidden}
.hero .side{top:0;height:437px;width:172px;background:linear-gradient(180deg,#8ed7e6,#3fb6d2)}
.hero .side.l{left:0}.hero .side.r{right:0}
.hero h1{left:172px;top:98px;font-size:35px;font-weight:900;color:var(--white);line-height:1.15;letter-spacing:.3px;white-space:nowrap}
.hero p{left:172px;top:188px;width:420px;font-size:16px;color:var(--white);line-height:1.3}
.btn{display:flex;align-items:center;justify-content:center;font-size:11px;font-weight:700}
.hero .btn-book{left:187px;top:270px;width:110px;height:36px;background:var(--dark);color:var(--white)}
.hero .btn-contact{left:305px;top:270px;width:105px;height:36px;background:var(--white);color:var(--ink)}
.collage{left:648px;top:48px;width:380px;height:342px;display:grid;grid-template-columns:repeat(3,1fr);grid-template-rows:repeat(3,1fr);gap:6px}
.collage div{background:linear-gradient(160deg,#e9eef1,#b8c4cc)}
.collage div:nth-child(2n){background:linear-gradient(160deg,#d9e3e8,#9fb0bb)}
.collage div:nth-child(5){background:linear-gradient(160deg,#c9d5dc,#7e93a0)}

/* section heading */
.kicker{width:100%;text-align:center;font-size:21px;color:var(--cyan);font-weight:400}
.title{width:100%;text-align:center;font-size:34px;font-weight:900;color:var(--dark)}
.divider{left:50%;margin-left:-160px;width:320px;height:24px}
.divider::before{content:"";position:absolute;left:0;right:0;top:11px;border-top:1px solid #c9eef6}
.divider span{position:absolute;left:148px;top:0;width:24px;height:24px;border-radius:50%;border:2px solid var(--cyan);background:var(--white)}
.divider span::after{content:"";position:absolute;left:6px;top:6px;width:8px;height:8px;border-radius:50%;background:var(--cyan)}

/* intro */
.intro{top:612px;height:621px}
.intro .kicker{top:65px}
.intro .title{top:90px}
.intro .divider{top:142px}
.intro .lead{top:180px;width:100%;text-align:center;font-size:15px;font-weight:700;color:var(--dark)}
.intro .copy{top:210px;left:172px;width:856px;font-size:11.5px;line-height:1.55;color:var(--muted)}
.video{left:172px;top:292px;width:856px;height:265px;background:linear-gradient(100deg,#dff2f8 0%,#a9dcec 55%,#eef8fb 100%)}
.video .frame{left:26px;top:14px;right:26px;bottom:14px;border:2px solid rgba(255,255,255,.85)}
.video .play{left:404px;top:108px;width:48px;height:48px;border-radius:50%;background:rgba(60,60,60,.55)}

/* why choose */
.why{top:1233px;height:558px;background:var(--cyan)}
.why .kicker{top:43px;color:var(--white)}
.why .title{top:68px;color:var(--white)}
.why .divider{top:120px}
.why .divider::before{border-color:rgba(255,255,255,.5)}
.why .divider span{background:var(--cyan);border-color:var(--white)}
.why .divider span::after{background:var(--white)}
.why .copy{top:150px;left:172px;width:856px;text-align:center;font-size:11px;line-height:1.5;color:var(--white)}
.why .photo{left:172px;top:224px;width:342px;height:265px;background:var(--white);padding:9px}
.why .photo div{width:100%;height:100%;background:linear-gradient(120deg,#f2efec,#d9cfc8 60%,#a7b6bf)}
.feature{width:240px;display:flex;gap:14px;color:var(--white)}
.feature .icon{flex:none;width:62px;height:62px;border-radius:50%;border:2px solid var(--white);display:flex;align-items:center;justify-content:center}
.feature h3{font-size:21px;font-weight:700;margin-top:8px}
.feature p{font-size:11px;line-height:1.4;margin-top:4px}
.why .vline{left:784px;top:232px;height:250px;border-left:1px solid rgba(255,255,255,.45)}
.why .hline{left:540px;top:356px;width:488px;border-top:1px solid rgba(255,255,255,.45)}

/* how it works */
.how{top:1791px;height:560px}
.how .kicker,.how .title{text-align:left;left:172px;width:auto}
.how .kicker{top:44px}
.how .title{top:68px}
.how .divider{left:172px;margin:0;width:260px;top:118px}
.how .divider span{left:62px}
.how .copy{top:152px;left:172px;width:856px;font-size:11.5px;line-height:1.55;color:var(--muted)}
.how .band{left:0;top:234px;width:475px;height:318px;background:var(--cyan)}
.how .photo{left:172px;top:259px;width:303px;height:268px;background:linear-gradient(135deg,#e8f3f7,#9ec6d5 55%,#5e8ea3)}
.how .text{left:540px;top:268px;width:488px;font-size:11.5px;line-height:1.6;color:var(--muted)}
.how .more{left:540px;top:478px;width:110px;height:34px;background:var(--cyan);color:var(--white)}

/* compare */
.compare{top:2390px;height:591px;background:linear-gradient(180deg,#f4f5f6,#e6eaec)}
.compare .ghost{left:0;top:0;width:1200px;height:591px;background:linear-gradient(90deg,rgba(200,208,212,.35),rgba(235,238,240,.2) 50%,rgba(200,208,212,.35))}
.compare .kicker{top:55px;color:var(--dark);font-size:20px}
.compare .title{top:80px}
.compare .divider{top:130px}
.compare .divider span{background:#f2f3f4}
.compare .copy{top:160px;left:172px;width:856px;text-align:center;font-size:11px;line-height:1.5;color:var(--ink)}
.table{left:172px;top:226px;width:856px;height:302px;display:grid;grid-template-columns:repeat(5,1fr);box-shadow:0 6px 14px rgba(0,0,0,.18)}
.col{display:flex;flex-direction:column;font-size:10px;color:var(--white);text-align:center}
.col .head{height:60px;display:flex;flex-direction:column;align-items:center;justify-content:center;font-size:12px;font-weight:700;border-bottom:1px solid rgba(255,255,255,.25)}
.col .head small{font-size:8px;font-weight:400;margin-top:2px}
.col .cell{flex:1;display:flex;align-items:center;justify-content:center;border-bottom:1px solid rgba(255,255,255,.18)}
.col.cyan{background:var(--cyan)}
.col.dark{background:var(--dark)}
.col.featured{background:var(--cyan-deep);margin:-10px 0;padding:10px 0;box-shadow:0 0 12px rgba(0,0,0,.25);position:relative;z-index:1}
.col.cyan .head{background:#2eb3cf}
.col.dark .head{background:#222}

/* testimonials */
.reviews{top:2981px;height:501px}
.reviews .kicker,.reviews .title{text-align:left;left:172px;width:auto}
.reviews .kicker{top:55px}
.reviews .title{top:80px}
.reviews .divider{left:172px;margin:0;width:260px;top:130px}
.reviews .divider span{left:62px}
.reviews .copy{top:162px;left:172px;width:856px;font-size:11px;line-height:1.5;color:var(--ink)}
.arrows{left:972px;top:208px;display:flex;gap:6px}
.arrows span{width:24px;height:22px;background:var(--dark);display:flex;align-items:center;justify-content:center}
.card-photo{top:262px;width:157px;height:169px}
.card-photo.a{left:172px;background:linear-gradient(150deg,#c8d3d9,#6f8795)}
.card-photo.b{left:637px;background:linear-gradient(150deg,#d7e3ea,#7d9fb4)}
.quote{font-size:44px;font-weight:900;color:var(--dark);line-height:1}
.rev-text{width:200px;font-size:12px;line-height:1.45;color:var(--ink)}
.stars{display:flex;gap:3px}
.rev-name{font-size:12px;font-weight:700;color:var(--dark);white-space:nowrap}

/* footer */
.sitefoot{top:3482px;height:329px;background:var(--footer);color:var(--white)}
.sitefoot h4{font-size:19px;font-weight:700;letter-spacing:.5px}
.about{left:172px;top:57px;width:270px}
.about p{font-size:10.5px;line-height:1.5;margin-top:36px}
.about ul{list-style:none;margin-top:26px;font-size:9.5px}
.about li{display:flex;align-items:center;gap:8px;margin-bottom:15px;white-space:nowrap}
.news{left:525px;top:57px;width:270px}
.news .field{margin-top:40px;width:265px;height:44px;border-radius:22px;background:#eee;color:#777;font-size:10px;display:flex;align-items:center;padding-left:22px}
.news .sub{margin-top:6px;width:137px;height:34px;border-radius:17px;background:var(--cyan);font-size:12px;font-weight:700;display:flex;align-items:center;justify-content:center}
.news .networks{margin-top:18px;display:flex;gap:10px;font-size:10px;color:#d6d6d6}
.quick{left:832px;top:57px;width:200px}
.quick .links{margin-top:34px;display:grid;grid-template-columns:1fr 1fr;row-gap:18px;font-size:9.5px}
.copyright{top:3811px;left:0;width:1200px;height:43px;background:var(--cyan);color:var(--white);font-size:10px}
.copyright .l{left:172px;top:16px;white-space:nowrap}
.copyright .r{right:172px;top:16px;white-space:nowrap}
</style>
</head>
<body>

<div class="topbar abs">
  <div class="hours abs"><b>Clinic Open</b> : Mon-Fri <b>9:15 am</b> to <b>5:30 pm</b> Sat <b>10am</b> to <b>2 pm</b> &nbsp;|&nbsp; <b>Book Appointments</b> : Mon-Fri 8:00 am to 3 pm</div>
  <div class="social abs"><span>Friendbook</span><span>Photogram</span><span>Chirper</span><span>Rateway</span></div>
</div>

<header class="masthead">
  <div class="logo abs">
    <div class="dot"></div>
    <div class="name">Bright Harbor<small>Smile Studio</small></div>
  </div>
  <div class="contact-item contact-address abs">
    <svg width="18" height="24" viewBox="0 0 18 24"><path d="M9 0C4 0 0 4 0 9c0 7 9 15 9 15s9-8 9-15c0-5-4-9-9-9zm0 13a4 4 0 110-8 4 4 0 010 8z" fill="#36c0dc"/></svg>
    <div><strong>ADDRESS</strong>1480 Harbor View Rd. #210 Bayside, CA 90000</div>
  </div>
  <div class="contact-item contact-phone abs">
    <svg width="20" height="20" viewBox="0 0 24 24"><path d="M6.6 10.8a15.1 15.1 0 006.6 6.6l2.2-2.2c.3-.3.7-.4 1-.2 1.1.4 2.3.6 3.6.6.6 0 1 .4 1 1V20c0 .6-.4 1-1 1C10.6 21 3 13.4 3 4c0-.6.4-1 1-1h3.5c.6 0 1 .4 1 1 0 1.3.2 2.5.6 3.6.1.3 0 .7-.2 1z" fill="#36c0dc"/></svg>
    <div><strong>PHONE</strong>+1-555-260-0149</div>
  </div>
</header>

<nav class="mainnav">
  <ul class="caps">
    <li>Home</li><li>Our Process</li><li>Photos</li><li>Free Treatments</li><li>Testimonials</li><li>Blog</li><li>FAQ</li><li>Contact</li><li>Gift Certificates</li>
  </ul>
  <div class="book caps">Book Appointment</div>
</nav>

<section class="hero">
  <div class="side l abs" role="img" aria-label="Faded customer smile photos"></div>
  <div class="side r abs" role="img" aria-label="Faded customer smile photos"></div>
  <h1 class="abs caps">Get That White Smile<br>You've Always Wanted</h1>
  <p class="abs">Amazing Results, The Most Effective System, More Affordable Than The Dentist.</p>
  <div class="btn btn-book abs caps">Book Online</div>
  <div class="btn btn-contact abs caps">Contact Us</div>
  <div class="collage abs" role="img" aria-label="Collage of happy customer photos holding review signs">
    <div></div><div></div><div></div><div></div><div></div><div></div><div></div><div></div><div></div>
  </div>
</section>

<section class="intro">
  <div class="kicker abs caps">Bright Harbor's</div>
  <h2 class="title abs caps">Smile Studio</h2>
  <div class="divider abs"><span></span></div>
  <div class="lead abs caps">The Best Price, Service and Results.</div>
  <p class="copy abs">Bright Harbor Smile Studio features state-of-the-art methods that are safe, gentle and very cost-effective. Our whitening system uses the latest blue light whitening technology. Our Blue Light Systems are tuned precisely for the best activation of our own hydrogen peroxide based whitening gel, which is made in a registered facility in the USA.</p>
  <div class="video abs" role="img" aria-label="Video still of a white tooth model with dental tools">
    <div class="frame abs"></div>
    <div class="play abs"><svg width="48" height="48" viewBox="0 0 48 48"><path d="M19 15l15 9-15 9z" fill="#fff"/></svg></div>
  </div>
</section>

<section class="why">
  <div class="kicker abs caps">Bright Harbor's</div>
  <h2 class="title abs caps">Why Choose Us</h2>
  <div class="divider abs"><span></span></div>
  <p class="copy abs">Lorem Ipsum is simply dummy text of the printing and typesetting industry. Lorem Ipsum has been the industry's standard dummy text ever since the Lorem Ipsum is simply dummy text of the printing and typesetting industry. Lorem Ipsum has been the industry's standard dummy text ever since the.</p>
  <div class="photo abs"><div role="img" aria-label="Smiling woman holding a whitening tray"></div></div>
  <div class="vline abs"></div><div class="hline abs"></div>
  <div class="feature abs" style="left:540px;top:250px">
    <div class="icon"><svg width="26" height="30" viewBox="0 0 26 30"><text x="13" y="24" text-anchor="middle" font-family="Roboto,Arial,sans-serif" font-size="26" font-weight="700" fill="#fff">$</text></svg></div>
    <div><h3 class="caps">Price</h3><p>Lorem Ipsum is simply dummy text of the printing and.</p></div>
  </div>
  <div class="feature abs" style="left:800px;top:250px">
    <div class="icon"><svg width="28" height="28" viewBox="0 0 28 28" fill="none" stroke="#fff" stroke-width="3"><path d="M11 17l6-6M9 13l-3 3a4 4 0 006 6l3-3M19 15l3-3a4 4 0 00-6-6l-3 3"/></svg></div>
    <div><h3 class="caps">No Pain</h3><p>Lorem Ipsum is simply dummy text of the printing and.</p></div>
  </div>
  <div class="feature abs" style="left:540px;top:378px">
    <div class="icon"><svg width="28" height="26" viewBox="0 0 28 26" fill="#fff"><rect x="2" y="14" width="5" height="10"/><rect x="9" y="8" width="5" height="16"/><rect x="16" y="11" width="5" height="13"/><rect x="23" y="4" width="4" height="20"/></svg></div>
    <div><h3 class="caps">Result</h3><p>Lorem Ipsum is simply dummy text of the printing and.</p></div>
  </div>
  <div class="feature abs" style="left:800px;top:378px">
    <div class="icon"><svg width="26" height="28" viewBox="0 0 26 28" fill="none" stroke="#fff" stroke-width="2.5"><path d="M5 20V12a8 8 0 0116 0v8l2 3H3z"/><path d="M10 25a3 3 0 006 0"/></svg></div>
    <div><h3 class="caps">Convenience</h3><p>Lorem Ipsum is simply dummy text of the printing and.</p></div>
  </div>
</section>

<section class="how">
  <div class="kicker abs caps">Bright Harbor's</div>
  <h2 class="title abs caps">How It Work</h2>
  <div class="divider abs"><span></span></div>
  <p class="copy abs">We have a very effective whitening treatment that is designed to give you quick results in about 1 hour. To start the treatment you will apply a peroxide based whitening gel to your teeth. We then place our cool blue light directly in front of your teeth for 15 minutes per treatment. The light activates the whitening gel and speeds up the whitening process, giving you whiter teeth in less than an hour.</p>
  <div class="band abs"></div>
  <div class="photo abs" role="img" aria-label="Dentist showing a patient a dental x-ray on a tablet"></div>
  <p class="text abs">We always perform what we call a "Triple Treatment". So that's 3 of the 15 minute treatments all done back to back in the same visit. The whole whitening time is a total of 45 minutes. Now there is a short break between each 15 minute session, and this is when we tell all our clients to give themselves one hour at the office. The biggest benefit of an in office treatment versus a take home kit is that you will see results right after the session. We also include our home care kit for after care. It is very important that no matter where you get your teeth whitened you keep up the results for the long term. You'll use our care kit once or twice per month as a touch up to help keep your new whitened teeth, and that will make your results last longer.</p>
  <div class="btn more abs caps">Read More</div>
</section>

<section class="compare">
  <div class="ghost abs" role="img" aria-label="Faded collage of customer photos"></div>
  <div class="kicker abs caps">Bright Harbor's</div>
  <h2 class="title abs caps">Compare Us</h2>
  <div class="divider abs"><span></span></div>
  <p class="copy abs">Lorem Ipsum is simply dummy text of the printing and typesetting industry. Lorem Ipsum has been the industry's standard dummy text ever since the Lorem Ipsum is simply dummy text of the printing and typesetting industry. Lorem Ipsum has been the industry's standard dummy text ever since the.</p>
  <div class="table abs caps">
    <div class="col cyan"><div class="head">Features</div><div class="cell">Speed</div><div class="cell">Ease of Use</div><div class="cell">Cost</div><div class="cell">Availability</div><div class="cell">Pain</div></div>
    <div class="col dark"><div class="head">GlowPro</div><div class="cell">1-2 Hours</div><div class="cell">Difficult / Dentist</div><div class="cell">$300 - $600</div><div class="cell">Limited Availability</div><div class="cell">Pain &amp; Sensitivity</div></div>
    <div class="col featured"><div class="head">Bright Harbor's<small>Smile Studio</small></div><div class="cell">45 Mins</div><div class="cell">Very Easy</div><div class="cell">$178</div><div class="cell">Appt Only</div><div class="cell">No Pain</div></div>
    <div class="col dark"><div class="head">LumaBright</div><div class="cell">7-14 Days</div><div class="cell">Difficult / Dentist</div><div class="cell">$300 - $600</div><div class="cell">Limited Availability</div><div class="cell">Sensitivity</div></div>
    <div class="col cyan"><div class="head">Home Kits</div><div class="cell">7-30 Days</div><div class="cell">Difficult</div><div class="cell">$50 - $140</div><div class="cell">Store Purchase</div><div class="cell">Sensitivity</div></div>
  </div>
</section>

<section class="reviews">
  <div class="kicker abs caps">Our Client Says</div>
  <h2 class="title abs caps">Tetstimonial</h2>
  <div class="divider abs"><span></span></div>
  <p class="copy abs">Lorem Ipsum is simply dummy text of the printing and typesetting industry. Lorem Ipsum has been the industry's standard dummy text ever since the. Lorem Ipsum is simply dummy text of the printing and typesetting industry. Lorem Ipsum has been the industry's standard dummy text ever since the.</p>
  <div class="arrows abs">
    <span><svg width="8" height="10" viewBox="0 0 8 10"><path d="M6 0L1 5l5 5" stroke="#fff" stroke-width="2" fill="none"/></svg></span>
    <span><svg width="8" height="10" viewBox="0 0 8 10"><path d="M2 0l5 5-5 5" stroke="#fff" stroke-width="2" fill="none"/></svg></span>
  </div>

  <div class="card-photo a abs" role="img" aria-label="Portrait of a smiling client"></div>
  <div class="quote abs" style="left:352px;top:262px">&ldquo;</div>
  <p class="rev-text abs" style="left:378px;top:276px">Lorem Ipsum is simply dummy text of the printing and typesetting industry. Lorem Ipsum has been the industry's standard dummyhe.</p>
  <div class="quote abs" style="left:585px;top:356px">&rdquo;</div>
  <div class="stars abs" style="left:378px;top:386px">
    <svg width="76" height="13" viewBox="0 0 76 13" fill="#2d2d2d"><g id="s"><path d="M6.5 0l1.9 4.2 4.6.4-3.5 3 1.1 4.5-4.1-2.4-4.1 2.4 1.1-4.5-3.5-3 4.6-.4z"/></g><use href="#s" x="15.5"/><use href="#s" x="31"/><use href="#s" x="46.5"/><use href="#s" x="62"/></svg>
  </div>
  <div class="rev-name abs caps" style="left:378px;top:410px">Jhon Marlo</div>

  <div class="card-photo b abs" role="img" aria-label="Portrait of a smiling client on the phone"></div>
  <div class="quote abs" style="left:816px;top:262px">&ldquo;</div>
  <p class="rev-text abs" style="left:842px;top:276px;width:186px">Lorem Ipsum is simply dummy text of the printing and typesetting industry. Lorem Ipsum has been the industry's standard dummyhe.</p>
  <div class="quote abs" style="left:1008px;top:356px">&rdquo;</div>
  <div class="stars abs" style="left:842px;top:386px">
    <svg width="76" height="13" viewBox="0 0 76 13" fill="#2d2d2d"><use href="#s"/><use href="#s" x="15.5"/><use href="#s" x="31"/><use href="#s" x="46.5"/><use href="#s" x="62"/></svg>
  </div>
  <div class="rev-name abs caps" style="left:842px;top:410px">Devin Tarlow</div>
</section>

<footer class="sitefoot">
  <div class="about abs">
    <h4 class="caps">About Us :</h4>
    <p>Lorem ipsum dolor sit amet, consectetur adipiscing elit. Vestibulum sollicitudin at risus non viverra. Curabitur hendrerit dolor arcu, ac porttitor arcu sagittis in.</p>
    <ul>
      <li><svg width="10" height="10" viewBox="0 0 24 24"><path d="M6.6 10.8a15.1 15.1 0 006.6 6.6l2.2-2.2c.3-.3.7-.4 1-.2 1.1.4 2.3.6 3.6.6.6 0 1 .4 1 1V20c0 .6-.4 1-1 1C10.6 21 3 13.4 3 4c0-.6.4-1 1-1h3.5c.6 0 1 .4 1 1 0 1.3.2 2.5.6 3.6.1.3 0 .7-.2 1z" fill="#fff"/></svg>1-555-260-0149</li>
      <li><svg width="11" height="9" viewBox="0 0 22 16"><rect width="22" height="16" fill="#fff"/><path d="M0 0l11 9 11-9" stroke="#5b5b5b" stroke-width="2" fill="none"/></svg>INFO@BRIGHTHARBORSMILESTUDIO.EXAMPLE</li>
      <li><svg width="9" height="12" viewBox="0 0 18 24"><path d="M9 0C4 0 0 4 0 9c0 7 9 15 9 15s9-8 9-15c0-5-4-9-9-9z" fill="#fff"/></svg>1480 HARBOR VIEW RD. #210, BAYSIDE, CA 90000</li>
    </ul>
  </div>
  <div class="news abs">
    <h4 class="caps">News Letter :</h4>
    <div class="field caps">Enter your email id</div>
    <div class="sub caps">Subscribe</div>
    <div class="networks"><span>Friendbook</span><span>Chirper</span><span>Linkup</span><span>Vidtube</span><span>Searchly</span></div>
  </div>
  <div class="quick abs">
    <h4 class="caps">Quick Link :</h4>
    <div class="links caps">
      <span>Home</span><span>Testimonials</span>
      <span>Our Process</span><span>Blog</span>
      <span>Photos</span><span>FAQ</span>
      <span>Free Treatments</span><span>Contact</span>
    </div>
  </div>
</footer>

<div class="copyright abs caps">
  <div class="l abs">© 2018 Bright Harbor Smile Studio. All Rights Reserved.</div>
  <div class="r abs">Gift Certificates</div>
</div>

</body>
</html>
```